Corporate-Design für Steuerberatungsgesellschaft
Zielgruppe
Wir sind eine Steuerberatungsgesellschaft mit 10 Mitarbeitern im Norden von Deutschland, kurz vor der Ostseeküste. Unser Unternehmen besteht seit 30 Jahren. Wir betreuen vor allem Mandanten in kleinen und mittleren Unternehmen: von der Arztpraxis bis zum Bauunternehmen. Demnächst werden wir neue Räume beziehen. Diese sollen großzügiger und moderner werden, teilweise mit Glaswänden.
Aufgabenstellung
Unser bisheriges Farbkonzept war von bordeaux und creme geprägt (www.kanzlei-mervato.de). Das muss aber nicht weiter bestehen. Das bisherige Logo finden wir inhaltlich recht treffend, aber es sollte moderner gestaltet werden. Der Schriftzug des Kanzleinamens soll an der Fassade in silbernen Buchstaben angebracht werden.

```html
<!DOCTYPE html>
<html lang="de">
<head>
<meta charset="utf-8">
<title>KBR Halden – Visitenkarte</title>
<link rel="stylesheet" href="https://fonts.googleapis.com/css2?family=Noto+Serif:wght@400;700&display=swap">
<style>
  :root {
    --bg: #c9c9cc;
    --card-dark: #1e1c1d;
    --card-light: #ffffff;
    --bordeaux: #8c1427;
    --ink: #3a3a3a;
    --muted: #6b6b6b;
    --white: #ffffff;
  }
  * { margin: 0; padding: 0; box-sizing: border-box; }
  html, body { width: 1200px; height: 852px; overflow: hidden; }
  body {
    background: var(--bg);
    font-family: "Noto Serif", Georgia, serif;
    position: relative;
  }
  .card {
    position: absolute;
    top: 271px;
    width: 480px;
    height: 310px;
    box-shadow: 0 6px 18px rgba(0,0,0,0.18);
  }
  /* Front */
  .card-front { left: 90px; background: var(--card-dark); }
  .front-band {
    position: absolute; left: 0; right: 0; bottom: 14px;
    height: 10px; background: var(--bordeaux);
  }
  .front-brand {
    position: absolute; left: 36px; bottom: 46px;
    display: flex; align-items: center; gap: 14px;
  }
  .brand-square {
    width: 34px; height: 34px;
    border: 2px solid var(--white); border-radius: 4px;
  }
  .brand-name-front {
    color: var(--white); font-size: 40px; font-weight: 400;
    letter-spacing: 0.02em; line-height: 1;
  }
  /* Back */
  .card-back { left: 630px; background: var(--card-light); }
  .back-brand {
    position: absolute; left: 30px; top: 132px;
    display: flex; align-items: center; gap: 8px;
  }
  .brand-square-dark {
    width: 22px; height: 22px;
    border: 2px solid var(--ink); border-radius: 3px;
  }
  .brand-name-back { color: var(--ink); font-size: 18px; font-weight: 400; }
  .details { position: absolute; left: 188px; top: 30px; right: 18px; }
  .degree { font-size: 10px; color: var(--muted); }
  .person-name {
    font-size: 20px; font-weight: 700; color: var(--bordeaux);
    line-height: 1.15; white-space: nowrap;
  }
  .person-role { font-size: 10px; color: var(--muted); margin-top: 2px; }
  .divider {
    height: 2px; background: var(--bordeaux);
    margin: 6px -18px 22px 0;
  }
  .company { font-size: 10px; line-height: 1.55; color: var(--ink); }
  .company-name { font-weight: 700; }
  .company-name .accent { color: var(--bordeaux); }
  .contacts { list-style: none; margin-top: 14px; font-size: 10px; color: var(--ink); }
  .contacts li { display: flex; align-items: center; gap: 8px; line-height: 1.75; }
  .contact-icon {
    width: 12px; height: 12px; border-radius: 50%;
    background: var(--bordeaux); display: flex; align-items: center; justify-content: center;
  }
  .contact-icon svg { width: 8px; height: 8px; }
</style>
</head>
<body>
  <section class="card card-front" aria-label="Vorderseite">
    <div class="front-brand">
      <span class="brand-square"></span>
      <span class="brand-name-front">KBR Halden</span>
    </div>
    <div class="front-band"></div>
  </section>

  <section class="card card-back" aria-label="Rückseite">
    <div class="back-brand">
      <span class="brand-square-dark"></span>
      <span class="brand-name-back">KBR Halden</span>
    </div>
    <div class="details">
      <p class="degree">Diplom-Kaufmann</p>
      <p class="person-name">Jonas Brenntal - Wiesel</p>
      <p class="person-role">Geschäftsführer / Steuerberater</p>
      <div class="divider"></div>
      <div class="company">
        <p class="company-name"><span class="accent">KBR</span> Halden</p>
        <p class="company-name">Steuerberatungsgesellschaft mbH</p>
        <p>Lindenweg 12</p>
        <p>17321 Feldrachen</p>
      </div>
      <ul class="contacts">
        <li><span class="contact-icon"><svg viewBox="0 0 10 10"><path d="M2 1l2 2-1 1.2c.6 1.2 1.5 2.1 2.8 2.8L7 6l2 2-1.2 1.2C4.5 9 1 5.5.8 2.2z" fill="#fff"/></svg></span>+49 (0) 3900 | 55 12 - 0</li>
        <li><span class="contact-icon"><svg viewBox="0 0 10 10"><rect x="2" y="1" width="6" height="3" fill="#fff"/><rect x="1" y="4.5" width="8" height="4" fill="#fff"/></svg></span>+49 (0) 3900 | 55 12 - 14</li>
        <li><span class="contact-icon"><svg viewBox="0 0 10 10"><rect x="1" y="2.5" width="8" height="5" fill="#fff"/><path d="M1 2.5l4 3 4-3" stroke="#8c1427" stroke-width="0.8" fill="none"/></svg></span>feldrachen@kanzlei-mervato.de</li>
        <li><span class="contact-icon"><svg viewBox="0 0 10 10"><circle cx="5" cy="5" r="3.6" stroke="#fff" stroke-width="0.9" fill="none"/><path d="M1.4 5h7.2M5 1.4c-1.8 2.2-1.8 5 0 7.2M5 1.4c1.8 2.2 1.8 5 0 7.2" stroke="#fff" stroke-width="0.7" fill="none"/></svg></span>www.kanzlei-mervato.de</li>
      </ul>
    </div>
  </section>
</body>
</html>
```